Verdanith Website Concept

We would like a one page website. Please refer to the attached files for more information.

Please reference file attachment version 1.1.

```html
<!DOCTYPE html>
<html lang="en">
<head>
<meta charset="utf-8">
<title>Verdanith</title>
<link rel="stylesheet" href="https://fonts.googleapis.com/css2?family=Arimo:ital,wght@0,400;0,700;1,400&family=Archivo+Black&display=swap">
<style>
:root{
  --ink:#444;
  --navy:#1f3a6b;
  --button:#2b3e6e;
  --logo:#56628c;
  --line:#cfcfcf;
  --panel:#f6f6f6;
  --icon:#a0a0a0;
  --white:#fff;
}
*{margin:0;padding:0;box-sizing:border-box}
html,body{width:1200px;height:1003px;overflow:hidden;background:var(--white)}
body{font-family:"Arimo",Arial,sans-serif;color:var(--ink)}
.page{position:absolute;left:0;top:0;width:1385px;height:1158px;transform:scale(.8664);transform-origin:0 0}
.abs{position:absolute}
.brand{left:200px;top:40px;display:flex;align-items:center;gap:12px}
.brand-dot{width:46px;height:46px;border-radius:50%;background:var(--logo)}
.brand-name{font-size:31px;color:var(--logo);letter-spacing:1px;text-transform:uppercase}
.nav{top:75px;font-size:12.5px;color:var(--ink);text-transform:uppercase}
.hero{left:201px;top:125px;width:1000px;height:435px;background:linear-gradient(100deg,#6f8fc8 0%,#5c7fc4 45%,#4f74c0 100%);overflow:hidden}
.hero-photo{position:absolute;left:0;top:0;width:540px;height:435px;background:linear-gradient(180deg,#5e7fbf 0%,#3a4456 45%,#22262e 100%)}
.hero-photo2{position:absolute;left:530px;top:230px;width:240px;height:205px;background:linear-gradient(180deg,#8fa6cf 0%,#33363c 60%,#1d1f24 100%)}
.hero-title{left:554px;top:92px;font-family:"Archivo Black",Arial,sans-serif;font-size:40px;color:var(--white);letter-spacing:1px}
.hero-text{left:555px;top:144px;width:400px;font-size:16.5px;line-height:25px;color:var(--white)}
.arrows{left:931px;top:392px;display:flex;gap:1px}
.arrows span{width:27px;height:27px;background:rgba(120,140,175,.55);display:flex;align-items:center;justify-content:center}
.shadow{left:0;top:520px;width:1385px;height:70px;background:radial-gradient(ellipse 50% 50% at 50% 50%,rgba(0,0,0,.55),rgba(0,0,0,0) 100%)}
.fade{left:201px;top:560px;width:1000px;height:80px;background:linear-gradient(#e3e3e3,#fff)}
.card{top:642px;width:233px}
.card-img{height:149px}
.card-title{margin:14px 2px 0;font-size:15px;line-height:20px;color:var(--navy)}
.card-link{margin-top:8px;font-size:12.5px;font-style:italic;color:var(--ink)}
.cta{left:201px;top:920px;width:1000px;height:88px;border:1px solid var(--line);background:var(--panel)}
.cta-text{position:absolute;left:34px;top:16px;width:700px;font-size:14px;line-height:26px}
.cta-btn{position:absolute;left:777px;top:22px;width:198px;height:42px;background:var(--button);color:var(--white);font-size:14.5px;display:flex;align-items:center;justify-content:center}
.footer{left:201px;top:1038px;width:1000px;height:90px;background:linear-gradient(#ececec,#fff)}
.footer-links{position:absolute;left:36px;top:27px;font-size:12.5px;word-spacing:0}
.footer-links span{margin-right:20px}
.copy{position:absolute;left:36px;top:58px;font-size:12.5px}
.follow{position:absolute;left:795px;top:43px;font-size:12.5px}
.social{position:absolute;left:860px;top:31px;display:flex;gap:9px}
.social span{width:32px;height:32px;border-radius:50%;background:var(--icon)}
</style>
</head>
<body>
<div class="page">
  <div class="abs brand"><span class="brand-dot"></span><span class="brand-name">Verdanith</span></div>
  <div class="abs nav" style="left:770px">Home</div>
  <div class="abs nav" style="left:869px">About Us</div>
  <div class="abs nav" style="left:994px">Services</div>
  <div class="abs nav" style="left:1118px">Contact Us</div>

  <div class="abs shadow"></div>
  <div class="abs fade"></div>
  <section class="abs hero">
    <div class="hero-photo" role="img" aria-label="Security guard in cap and dark uniform jacket against blue sky"></div>
    <div class="hero-photo2" role="img" aria-label="Second security guard holding a radio"></div>
    <h1 class="abs hero-title">VERDANITH</h1>
    <p class="abs hero-text">Verdanith is a United States-based tier one security firm specializing in the protection of financial services professionals</p>
    <div class="abs arrows">
      <span><svg width="8" height="12"><path d="M6 1 1 6l5 5" fill="none" stroke="#dfe6f2" stroke-width="1.2"/></svg></span>
      <span><svg width="8" height="12"><path d="M2 1l5 5-5 5" fill="none" stroke="#dfe6f2" stroke-width="1.2"/></svg></span>
    </div>
  </section>

  <div class="abs card" style="left:201px">
    <div class="card-img" role="img" aria-label="Man speaking into a two-way radio" style="background:linear-gradient(90deg,#3a3a3a,#b89a80 55%,#8a7a70)"></div>
    <div class="card-title">Threat Assessment</div>
    <div class="card-link">Click here for info &rsaquo;&rsaquo;</div>
  </div>
  <div class="abs card" style="left:458px">
    <div class="card-img" role="img" aria-label="Chain and combination padlock on a keyboard" style="background:linear-gradient(180deg,#2a2a2a,#8a8a8a 55%,#d8d8d8)"></div>
    <div class="card-title">Threat Avoidance Plan &amp; Dossier Creation</div>
    <div class="card-link">Click here for info &rsaquo;&rsaquo;</div>
  </div>
  <div class="abs card" style="left:713px">
    <div class="card-img" role="img" aria-label="Uniformed security officer in an airport corridor" style="background:linear-gradient(90deg,#c9d6e4,#9fb4d2 50%,#dde4ec)"></div>
    <div class="card-title">Elite Executive Protection</div>
    <div class="card-link">Click here for info &rsaquo;&rsaquo;</div>
  </div>
  <div class="abs card" style="left:968px">
    <div class="card-img" role="img" aria-label="Cupped hands around a seedling in soil" style="background:radial-gradient(circle at 55% 55%,#c8b07a,#7a6035 60%,#3d2e18)"></div>
    <div class="card-title">Threat Avoidance Plan &amp; Dossier Maintenance</div>
    <div class="card-link" style="margin-top:5px">Click here for info &rsaquo;&rsaquo;</div>
  </div>

  <section class="abs cta">
    <p class="cta-text">Verdanith is a United States-based tier one security firm specializing in the protection of financial services professionals, executives and their families.</p>
    <div class="cta-btn">CONTACT NOW</div>
  </section>

  <footer class="abs footer">
    <div class="footer-links"><span>Home</span><span>|</span><span>About us</span><span>|</span><span>Services</span><span>|</span><span>Contact us</span></div>
    <div class="copy">Copyright 2014. Verdanith. All rights reserved.</div>
    <div class="follow">Folow us :</div>
    <div class="social"><span></span><span></span><span></span></div>
  </footer>
</div>
</body>
</html>
```